New Business Card Design Project

Use the flyer uploaded and website www.brightoakbuilders.com for inspiration.
List Our Services on Backside of business cards
Marcus Delling
Harborline Builders Inc.
Licensed General Contractors
858-471-6093

Contact Information for Business Card

Use the flyer uploaded and website www.brightoakbuilders.com for inspiration. List Our Services on Backside of business cards Marcus Delling Harborline Builders Inc. Licensed General Contractors 858-471-6093

```html
<!DOCTYPE html>
<html lang="en">
<head>
<meta charset="utf-8">
<title>Harborline Builders – Business Card</title>
<link rel="stylesheet" href="https://fonts.googleapis.com/css2?family=Marcellus&family=Arimo:wght@400;700&display=swap">
<style>
  :root {
    --backdrop: #d9d9d9;
    --card-dark: #333333;
    --card-light: #f7f7f7;
    --ink-light: #ffffff;
    --ink-dark: #2b2b2b;
    --ink-soft: #4a4a4a;
  }
  * { margin: 0; padding: 0; box-sizing: border-box; }
  html, body { width: 1200px; height: 800px; overflow: hidden; }
  body {
    background: var(--backdrop);
    display: flex;
    align-items: center;
    justify-content: center;
    gap: 50px;
    font-family: "Arimo", Arial, sans-serif;
  }
  .card {
    width: 540px;
    height: 310px;
    border-radius: 22px;
    position: relative;
    box-shadow: 0 10px 24px rgba(0,0,0,0.18);
  }
  /* Front */
  .card-front { background: var(--card-dark); color: var(--ink-light); }
  .front-brand {
    position: absolute;
    top: 46px; right: 46px;
    display: flex; align-items: center; gap: 8px;
    font-family: "Marcellus", Georgia, serif;
    font-size: 13px; letter-spacing: 2px; text-transform: uppercase;
    white-space: nowrap;
  }
  .brand-square { width: 10px; height: 10px; border: 1px solid currentColor; }
  .holder-name {
    position: absolute; left: 150px; top: 128px;
    font-family: "Marcellus", Georgia, serif;
    font-size: 24px; letter-spacing: 3px; text-transform: uppercase; font-weight: 400;
    white-space: nowrap;
  }
  .name-rule {
    position: absolute; left: 40px; top: 178px;
    width: 70px; height: 1px; background: var(--ink-light);
  }
  .contact-list { position: absolute; left: 40px; top: 194px; list-style: none; font-size: 14.5px; line-height: 20px; }
  .contact-list b { font-weight: 700; margin-right: 4px; }
  .company-lines { position: absolute; left: 30px; top: 258px; font-size: 14.5px; line-height: 20px; }

  /* Back */
  .card-back { background: var(--card-light); color: var(--ink-dark); }
  .service-list {
    position: absolute; left: 30px; top: 30px;
    list-style: none; font-size: 15px; line-height: 27.5px;
    white-space: nowrap;
  }
  .service-list li::before {
    content: ""; display: inline-block;
    width: 8px; height: 8px; background: var(--ink-dark);
    margin-right: 12px; vertical-align: 1px;
  }
  .brand-lockup {
    position: absolute; right: 22px; top: 118px;
    width: 232px; text-align: center;
  }
  .brand-mark {
    width: 16px; height: 16px; border: 1.5px solid var(--ink-dark);
    margin: 0 auto 12px;
  }
  .brand-name {
    font-family: "Marcellus", Georgia, serif;
    font-size: 17px; letter-spacing: 0.5px; text-transform: uppercase; line-height: 1;
    white-space: nowrap;
  }
  .brand-web {
    font-family: "Marcellus", Georgia, serif;
    font-size: 10.5px; letter-spacing: 1.5px; text-transform: uppercase;
    color: var(--ink-soft); margin-top: 22px;
    white-space: nowrap;
  }
</style>
</head>
<body>
  <section class="card card-front">
    <div class="front-brand"><span class="brand-square"></span>Harborline Builders</div>
    <h1 class="holder-name">Marcus Delling</h1>
    <div class="name-rule"></div>
    <ul class="contact-list">
      <li><b>P :</b>858-471-6093</li>
      <li><b>E :</b>info@brightoakbuilders.com</li>
      <li><b>W :</b>www.brightoakbuilders.com</li>
    </ul>
    <div class="company-lines">
      <p>Harborline Builders Inc.</p>
      <p>Licensed General Contractors</p>
    </div>
  </section>

  <section class="card card-back">
    <ul class="service-list">
      <li>Remodeling : Kitchen &amp; Bath</li>
      <li>Painting : Interior &amp; Exterior</li>
      <li>Flooring : Carpet, Vinyl, Wood</li>
      <li>Window &amp; Door Replacement</li>
      <li>Plumbing : Repairs &amp; Upgrades</li>
      <li>Energy- Efficient Upgrades</li>
      <li>Deck &amp; Patio Construction</li>
      <li>Water &amp; Mold Damage</li>
      <li>Garage Renovation</li>
    </ul>
    <div class="brand-lockup">
      <div class="brand-mark"></div>
      <p class="brand-name">Harborline Builders</p>
      <p class="brand-web">www.brightoakbuilders.com</p>
    </div>
  </section>
</body>
</html>
```